Business Card Design Project

We need a Business Card for an Mechanical Engineering firm in Singapore. The design should be Modern & Technical looking, yet eye catching.

Our company deals in Cutting Tools & Machine Accessories for the Manufacturing Industries such as Oil & Gas, Aero Space, etc... For more information on our Company, you can either email me or view our website www.torvalen.com.sg.

We are trying to revamp our image to give our consumers a fresh new perspective to our company, so we welcome all ideas.

Industry/Entity Type

Business

Requirements
Must have
• Must incorporate New Company Logo into the card as shown in Uploaded file.

```html
<!DOCTYPE html>
<html lang="en">
<head>
<meta charset="UTF-8">
<title>Torvalen Tools – Business Card</title>
<link rel="stylesheet" href="https://fonts.googleapis.com/css2?family=Open+Sans:wght@300;400;600&display=swap">
<style>
  :root {
    --crimson: #9b0036;
    --crimson-faint: #a8264f;
    --paper: #f2f1ef;
    --stage: #e4e2de;
    --white: #ffffff;
  }
  * { margin: 0; padding: 0; box-sizing: border-box; }
  html, body { width: 1200px; height: 900px; overflow: hidden; }
  body {
    background: var(--stage);
    font-family: "Open Sans", Arial, sans-serif;
    display: flex;
    flex-direction: column;
    align-items: center;
    justify-content: center;
    gap: 60px;
  }
  .card {
    position: relative;
    width: 600px;
    height: 343px;
    overflow: hidden;
    box-shadow: 0 6px 18px rgba(0,0,0,0.18);
  }
  /* Front: crimson contact side */
  .card--front { background: var(--crimson); color: var(--white); }
  .card-front__decor {
    position: absolute;
    right: -70px;
    top: -60px;
    width: 330px;
    height: 330px;
  }
  .brand-mark {
    position: absolute;
    left: 48px;
    bottom: 56px;
    display: flex;
    align-items: center;
    gap: 10px;
  }
  .brand-mark__dot {
    width: 16px; height: 16px; border-radius: 50%;
    background: var(--white);
  }
  .brand-mark__name {
    font-weight: 600;
    font-size: 22px;
    letter-spacing: 2px;
    text-transform: uppercase;
    color: var(--white);
  }
  .contact {
    position: absolute;
    left: 300px;
    top: 92px;
    padding-left: 22px;
    border-left: 2px solid var(--white);
  }
  .contact__name {
    font-weight: 400;
    font-size: 22px;
    letter-spacing: 0.5px;
    text-transform: uppercase;
    margin-bottom: 14px;
  }
  .contact__line {
    font-weight: 400;
    font-size: 12.5px;
    line-height: 1.9;
  }
  .contact__label { display: inline-block; width: 24px; }
  /* Back: white logo side */
  .card--back { background: var(--paper); }
  .card-back__logo {
    position: absolute;
    inset: 0;
    display: flex;
    align-items: center;
    justify-content: center;
    gap: 20px;
  }
  .card-back__dot {
    width: 46px; height: 46px; border-radius: 50%;
    background: var(--crimson);
  }
  .card-back__name {
    font-weight: 600;
    font-size: 46px;
    letter-spacing: 3px;
    text-transform: uppercase;
    color: var(--crimson);
  }
</style>
</head>
<body>
  <section class="card card--front">
    <svg class="card-front__decor" viewBox="0 0 330 330" aria-hidden="true">
      <circle cx="165" cy="165" r="150" fill="var(--crimson-faint)" opacity="0.55"/>
    </svg>
    <div class="brand-mark">
      <span class="brand-mark__dot"></span>
      <span class="brand-mark__name">Torvalen Tools</span>
    </div>
    <div class="contact">
      <p class="contact__name">Marcus Henley</p>
      <p class="contact__line"><span class="contact__label">t :</span>6358 2140</p>
      <p class="contact__line"><span class="contact__label">f :</span>6358 2147</p>
      <p class="contact__line"><span class="contact__label">e :</span>daniel.koh@torvalen.com</p>
      <p class="contact__line"><span class="contact__label">w :</span>http://www.torvalentools.com</p>
    </div>
  </section>

  <section class="card card--back">
    <div class="card-back__logo">
      <span class="card-back__dot"></span>
      <span class="card-back__name">Torvalen Tools</span>
    </div>
  </section>
</body>
</html>
```